Looking for a cool & simple business-card-design for digital agency

Hi!

We are a web agency that offers Reputation Management, Vextor & Seo Services and software development. We like cool things, we like innovative styles.

We have uploaded our logo.

Project Deadline Extended Reason: Client does not want any designs with the colorful logo. Please send us submissions ONLY with the blac and white logo. What the client would like to see:1) Back of the card: is a silver logo on a black background2) front of the card with all the data, please use white background and black logo thank you Added Friday, May 8, 2015

Industry/Entity Type

Software

```html
<!DOCTYPE html>
<html lang="de">
<head>
<meta charset="utf-8">
<title>Lumora – Business Card</title>
<link href="https://fonts.googleapis.com/css2?family=Open+Sans:wght@400;600;700&display=swap" rel="stylesheet">
<style>
  :root {
    --bg-top: #cfcfcf;
    --bg-bottom: #f2f2f2;
    --card-black: #1f1f1f;
    --card-black-edge: #2b2b2b;
    --card-white: #f7f7f5;
    --silver: #b8b8b8;
    --ink: #232323;
    --ink-soft: #3a3a3a;
  }
  * { margin: 0; padding: 0; box-sizing: border-box; }
  html, body { width: 1200px; height: 900px; overflow: hidden; }
  body {
    background: linear-gradient(180deg, var(--bg-top), var(--bg-bottom));
    font-family: "Open Sans", sans-serif;
    position: relative;
  }
  .card {
    position: absolute;
    width: 560px;
    height: 350px;
    border-radius: 3px;
    box-shadow: 0 18px 40px rgba(0,0,0,0.22);
  }
  .card--back {
    left: 90px; top: 110px;
    background: linear-gradient(160deg, var(--card-black-edge), var(--card-black));
    display: flex; align-items: center; justify-content: center;
  }
  .card--front {
    left: 550px; top: 440px;
    background: var(--card-white);
    color: var(--ink);
  }
  .brand {
    display: flex; align-items: center; gap: 14px;
    font-weight: 700; letter-spacing: 0.5px;
  }
  .brand__mark { display: block; }
  .brand--silver { color: var(--silver); font-size: 50px; }
  .brand--silver .brand__mark { width: 34px; height: 34px; background: var(--silver); }
  .brand--ink { color: var(--ink); font-size: 36px; position: absolute; top: 42px; right: 40px; }
  .brand--ink .brand__mark { width: 24px; height: 24px; background: var(--ink); }
  .person { position: absolute; left: 40px; top: 44px; }
  .person__name { font-size: 20px; font-weight: 700; letter-spacing: 0.6px; text-transform: uppercase; }
  .person__role { font-size: 14px; color: var(--ink-soft); margin-top: -2px; }
  .contact { position: absolute; left: 40px; bottom: 38px; list-style: none; font-size: 15px; line-height: 20px; color: var(--ink-soft); }
  .contact li { display: flex; align-items: center; gap: 8px; }
  .contact svg { width: 13px; height: 13px; flex: none; }
  .address { position: absolute; right: 40px; bottom: 38px; text-align: right; font-size: 15px; line-height: 21px; color: var(--ink-soft); }
</style>
</head>
<body>
  <section class="card card--back" aria-label="Card back">
    <div class="brand brand--silver"><span class="brand__mark"></span>Lumora</div>
  </section>

  <section class="card card--front" aria-label="Card front">
    <div class="person">
      <div class="person__name">Jonas Berger</div>
      <div class="person__role">Managing Director</div>
    </div>
    <div class="brand brand--ink"><span class="brand__mark"></span>Lumora</div>

    <ul class="contact">
      <li>
        <svg viewBox="0 0 14 14"><rect width="14" height="14" rx="2" fill="#3a3a3a"/><path d="M4 3.5c.5-.4 1-.3 1.3.2l.6 1.2c.2.4 0 .8-.3 1l-.4.3c.4.9 1.1 1.6 2 2l.3-.4c.3-.3.7-.4 1-.2l1.2.6c.5.3.6.8.2 1.3-.7.8-1.8.9-3 .2C5.4 8.9 4.6 8.1 4 7c-.7-1.3-.7-2.7 0-3.5z" fill="#f7f7f5"/></svg>
        +49-(40)-5550-0142
      </li>
      <li>
        <svg viewBox="0 0 14 14"><rect width="14" height="14" rx="2" fill="#3a3a3a"/><rect x="4" y="3" width="6" height="3" fill="#f7f7f5"/><rect x="3" y="6.5" width="8" height="3" fill="#f7f7f5"/><rect x="4.5" y="9" width="5" height="2.5" fill="#f7f7f5"/></svg>
        +49-(40)-5550-0142
      </li>
      <li>
        <svg viewBox="0 0 14 14"><rect width="14" height="14" rx="2" fill="#3a3a3a"/><rect x="3" y="4" width="8" height="6" fill="none" stroke="#f7f7f5"/><path d="M3 4l4 3.5L11 4" fill="none" stroke="#f7f7f5"/></svg>
        jonas@lumora-ag.de
      </li>
      <li>
        <svg viewBox="0 0 14 14"><rect width="14" height="14" rx="2" fill="#3a3a3a"/><circle cx="7" cy="7" r="4" fill="none" stroke="#f7f7f5"/><ellipse cx="7" cy="7" rx="1.8" ry="4" fill="none" stroke="#f7f7f5"/><path d="M3 7h8" stroke="#f7f7f5"/></svg>
        www.lumora-ag.de
      </li>
    </ul>

    <address class="address" style="font-style:normal">
      Am Lindenhof 42<br>
      20095 Hamburg, Germany
    </address>
  </section>
</body>
</html>
```